Chimney Service company needs new business card design

We need a updated business card with our new logo added. We provide a full range of chimney services throughout Vermont and New Hampshire. The business card will be one sided and color. Attached is our current business card another document showing all the information we would like on the card.
We dont like a lot of flashy colors.... here is a link to our website to get an idea of our branding www.flueguardianvt.example

Target Market(s)

homeowners

Industry/Entity Type

Business

Contact Information for Business Card

See attached sheet for content.

Font styles to use
Serif
Sans Serif

Requirements
Must have
• all information provided on separate sheet
Should not have
• Additional information that may clogg up design

```html
<!DOCTYPE html>
<html lang="en">
<head>
<meta charset="utf-8">
<title>Flue Guardian – Business Card</title>
<link rel="stylesheet" href="https://fonts.googleapis.com/css2?family=Cinzel:wght@600&family=Questrial&display=swap">
<style>
  :root {
    --page-bg: #e9e6e1;
    --card-white: #f7f7f5;
    --panel-dark: #3a3b3d;
    --panel-dark-deep: #2b2c2e;
    --ink: #3b3b3b;
    --ink-soft: #5a5a5a;
    --accent-red: #9e1b22;
    --on-dark: #f3f3f3;
  }
  * { box-sizing: border-box; margin: 0; padding: 0; }
  html, body { width: 1200px; height: 1022px; overflow: hidden; }
  body {
    background: var(--page-bg);
    display: flex; align-items: center; justify-content: center;
    font-family: "Questrial", "Century Gothic", sans-serif;
  }
  .business-card {
    width: 900px; height: 514px;
    display: flex;
    background: var(--card-white);
    box-shadow: 0 18px 40px rgba(0,0,0,0.22);
  }
  .brand-panel {
    width: 330px; height: 100%;
    background: linear-gradient(135deg, var(--panel-dark) 0%, var(--panel-dark-deep) 100%);
    position: relative;
  }
  .brand-text {
    position: absolute; left: 50%; top: 50%;
    width: 440px;
    transform: translate(-50%, -50%) rotate(90deg);
    color: var(--on-dark);
    text-align: center;
  }
  .brand-name {
    font-family: "Cinzel", "Trajan Pro", serif;
    font-weight: 600; font-size: 36px; letter-spacing: 3px;
    white-space: nowrap;
  }
  .brand-year {
    margin-top: 10px;
    font-size: 16px; letter-spacing: 4px; text-transform: uppercase;
  }
  .info-panel {
    flex: 1; position: relative;
    padding: 62px 60px 0 64px;
    color: var(--ink);
  }
  .contact-list { list-style: none; display: grid; gap: 10px; }
  .contact-item {
    display: flex; align-items: center; gap: 14px;
    font-size: 23px; color: var(--ink-soft);
  }
  .contact-icon { width: 22px; height: 22px; flex: none; }
  .service-list { list-style: none; margin-top: 48px; display: grid; gap: 6px; }
  .service-item {
    font-size: 23px; letter-spacing: 1px; text-transform: uppercase;
    display: flex; align-items: center; gap: 12px;
  }
  .service-item::before, .service-sep {
    content: ""; width: 8px; height: 8px; border-radius: 50%;
    background: var(--accent-red); display: inline-block; flex: none;
  }
  .accent-line {
    position: absolute; left: 64px; right: 40px; bottom: 46px;
    height: 5px; background: var(--accent-red);
  }
</style>
</head>
<body>
  <article class="business-card">
    <section class="brand-panel">
      <div class="brand-text">
        <h1 class="brand-name">FLUE GUARDIAN</h1>
        <p class="brand-year">Est. 1994</p>
      </div>
    </section>
    <section class="info-panel">
      <ul class="contact-list">
        <li class="contact-item">
          <svg class="contact-icon" viewBox="0 0 22 22" aria-hidden="true"><circle cx="11" cy="11" r="11" fill="#9e1b22"/><path d="M7.5 6c.6-.5 1.3-.4 1.6.2l.8 1.5c.3.5.1 1-.3 1.3l-.5.4c.5 1.2 1.4 2.1 2.5 2.6l.4-.5c.3-.4.9-.5 1.3-.2l1.5.9c.6.3.6 1 .2 1.5-.9 1.1-2.2 1.2-3.6.4-1.9-1-3.4-2.6-4.2-4.5-.5-1.3-.4-2.6.3-3.6z" fill="#fff"/></svg>
          <span>802-555-0147</span>
        </li>
        <li class="contact-item">
          <svg class="contact-icon" viewBox="0 0 22 22" aria-hidden="true"><circle cx="11" cy="11" r="11" fill="#9e1b22"/><rect x="5.5" y="7" width="11" height="8" fill="none" stroke="#fff" stroke-width="1.3"/><path d="M5.5 7.5l5.5 4 5.5-4" fill="none" stroke="#fff" stroke-width="1.3"/></svg>
          <span>info@flueguardianvt.example</span>
        </li>
        <li class="contact-item">
          <svg class="contact-icon" viewBox="0 0 22 22" aria-hidden="true"><circle cx="11" cy="11" r="11" fill="#9e1b22"/><g fill="none" stroke="#fff" stroke-width="1.2"><circle cx="11" cy="11" r="5.5"/><ellipse cx="11" cy="11" rx="2.4" ry="5.5"/><path d="M5.5 11h11"/></g></svg>
          <span>www.flueguardianvt.example</span>
        </li>
      </ul>
      <ul class="service-list">
        <li class="service-item">Full Masonry Services</li>
        <li class="service-item">Historic Chimney Restoration</li>
        <li class="service-item">Stainless Steel Liners</li>
        <li class="service-item">Fully Certified Chimney Sweep</li>
        <li class="service-item">Fully Insured <span class="service-sep"></span> Free Estimates</li>
      </ul>
      <div class="accent-line" aria-hidden="true"></div>
    </section>
  </article>
</body>
</html>
```